Web Design Project

Hi, we need a new and professional design for our company "partnertradecircuitry". The website should communicate business but with a friendly and professional touch.

You can use the following categories for the menu;

Home - customer groups - products - voucher system- contact

Give it your best,

Regards,
Oswin

Industry/Entity Type

Business

```html
<!DOCTYPE html>
<html lang="en">
<head>
<meta charset="utf-8">
<title>partnertradecircuitry — Products</title>
<link rel="stylesheet" href="https://fonts.googleapis.com/css2?family=Arimo:wght@400;700&display=swap">
<style>
  :root {
    --ink: #000000;
    --paper: #ffffff;
    --accent: #1c8a1c;
    --accent-dark: #0f4f0f;
  }
  * { box-sizing: border-box; margin: 0; padding: 0; }
  html, body { width: 1200px; height: 900px; overflow: hidden; background: var(--ink); }
  body { font-family: "Arimo", Arial, sans-serif; color: var(--paper); }

  .page { position: relative; width: 1200px; height: 900px; overflow: hidden; background: var(--ink); }

  .brand {
    position: absolute; left: 30px; top: 128px;
    font-size: 25px; font-weight: 400; color: var(--paper);
  }

  .side-arc, .corner-sweep { position: absolute; left: 0; top: 0; }
  .corner-sweep { z-index: 3; }

  .main-nav { position: absolute; left: 0; top: 450px; width: 170px; }
  .main-nav a {
    position: absolute; left: 0; width: 165px; height: 56px;
    color: var(--paper); text-decoration: none; font-size: 19px; line-height: 1.05;
  }
  .main-nav a svg { position: absolute; left: 0; top: 0; }
  .main-nav a span { position: absolute; }
  .nav-home { top: 0; } .nav-home span { left: 36px; top: 16px; }
  .nav-groups { top: 66px; } .nav-groups span { left: 22px; top: 9px; font-size: 18px; text-align: center; }
  .nav-products { top: 137px; } .nav-products span { left: 23px; top: 16px; }
  .nav-voucher { top: 200px; } .nav-voucher span { left: 28px; top: 9px; font-size: 18px; text-align: center; }
  .nav-contact { top: 274px; } .nav-contact span { left: 28px; top: 16px; }

  .product-list { position: absolute; left: 316px; top: 42px; width: 769px; height: 815px; z-index: 5; }
  .product-card {
    position: absolute; left: 0; width: 769px; height: 181px;
    border: 3px solid var(--accent); border-left-color: var(--accent-dark); border-top-color: var(--accent-dark);
    border-radius: 14px; background: var(--ink);
  }
  .product-card:nth-child(1) { top: 0; }
  .product-card:nth-child(2) { top: 198px; }
  .product-card:nth-child(3) { top: 395px; }
  .product-card:nth-child(4) { top: 592px; }
  .product-image {
    position: absolute; left: 23px; top: 20px; width: 136px; height: 136px;
    background: var(--paper); color: var(--ink);
    display: flex; align-items: center; justify-content: center; text-align: center;
    font-size: 19px; font-weight: 700; line-height: 30px;
  }
  .product-info { position: absolute; left: 185px; top: 18px; width: 545px; font-weight: 700; }
  .product-title { font-size: 19px; line-height: 22px; margin: 0 0 8px 2px; }
  .product-cost { font-size: 19px; line-height: 22px; margin-bottom: 6px; }
  .product-desc { font-size: 19px; line-height: 26px; }

  .corner-name {
    position: absolute; left: 1118px; top: 600px; z-index: 4;
    writing-mode: vertical-rl; font-size: 26px; font-weight: 400; color: var(--ink);
  }

  .copyright { position: absolute; left: 293px; top: 873px; font-size: 14px; font-weight: 700; }
</style>
</head>
<body>
<div class="page">
  <div class="brand">partnertradecircuitry</div>

  <svg class="side-arc" width="300" height="900" viewBox="0 0 300 900" aria-hidden="true">
    <path d="M0,300 C165,312 272,560 270,900 L256,900 C258,585 150,330 0,310 Z" fill="#ffffff"/>
  </svg>

  <nav class="main-nav">
    <a class="nav-home" href="#">
      <svg width="165" height="56" viewBox="0 0 165 56"><path d="M20,6 C110,0 170,20 150,42 C140,52 120,54 100,54 C130,48 150,36 140,22 C128,10 70,4 20,6 Z" fill="#ffffff"/></svg>
      <span>Home</span></a>
    <a class="nav-groups" href="#">
      <svg width="165" height="56" viewBox="0 0 165 56"><path d="M20,6 C110,0 170,20 150,42 C140,52 120,54 100,54 C130,48 150,36 140,22 C128,10 70,4 20,6 Z" fill="#ffffff"/></svg>
      <span>Customer<br>&nbsp;&nbsp;Groups</span></a>
    <a class="nav-products" href="#">
      <svg width="165" height="56" viewBox="0 0 165 56"><path d="M20,6 C110,0 170,20 150,42 C140,52 120,54 100,54 C130,48 150,36 140,22 C128,10 70,4 20,6 Z" fill="#1c8a1c"/></svg>
      <span>Products</span></a>
    <a class="nav-voucher" href="#">
      <svg width="165" height="56" viewBox="0 0 165 56"><path d="M20,6 C110,0 170,20 150,42 C140,52 120,54 100,54 C130,48 150,36 140,22 C128,10 70,4 20,6 Z" fill="#ffffff"/></svg>
      <span>Voucher<br>&nbsp;&nbsp;System</span></a>
    <a class="nav-contact" href="#">
      <svg width="165" height="56" viewBox="0 0 165 56"><path d="M20,6 C110,0 170,20 150,42 C140,52 120,54 100,54 C130,48 150,36 140,22 C128,10 70,4 20,6 Z" fill="#ffffff"/></svg>
      <span>Contact</span></a>
  </nav>

  <section class="product-list">
    <article class="product-card">
      <div class="product-image" role="img" aria-label="Product photo">Product<br>Image</div>
      <div class="product-info">
        <h2 class="product-title">Product Title</h2>
        <p class="product-cost">$cost</p>
        <p class="product-desc">product description here. Talk about size, shape, color,<br>uses.&nbsp; Room for anything else that could say about the<br>product</p>
      </div>
    </article>
    <article class="product-card">
      <div class="product-image" role="img" aria-label="Product photo">Product<br>Image</div>
      <div class="product-info">
        <h2 class="product-title">Product Title</h2>
        <p class="product-cost">$cost</p>
        <p class="product-desc">product description here. Talk about size, shape, color,<br>uses.&nbsp; Room for anything else that could say about the<br>product</p>
      </div>
    </article>
    <article class="product-card">
      <div class="product-image" role="img" aria-label="Product photo">Product<br>Image</div>
      <div class="product-info">
        <h2 class="product-title">Product Title</h2>
        <p class="product-cost">$cost</p>
        <p class="product-desc">product description here. Talk about size, shape, color,<br>uses.&nbsp; Room for anything else that could say about the<br>product</p>
      </div>
    </article>
    <article class="product-card">
      <div class="product-image" role="img" aria-label="Product photo">Product<br>Image</div>
      <div class="product-info">
        <h2 class="product-title">Product Title</h2>
        <p class="product-cost">$cost</p>
        <p class="product-desc">product description here. Talk about size, shape, color,<br>uses.&nbsp; Room for anything else that could say about the<br>product</p>
      </div>
    </article>
  </section>

  <svg class="corner-sweep" width="1200" height="900" viewBox="0 0 1200 900" aria-hidden="true">
    <path d="M1200,486 C1050,650 820,800 550,900 L1200,900 Z" fill="#ffffff"/>
  </svg>
  <div class="corner-name">partnertradecircuitry</div>

  <footer class="copyright">Copyright 2013</footer>
</div>
</body>
</html>
```